Social Media Graphics - Oakline Push REVISED

Create 6-7 individual social media graphics (square size) to encourage folks to join our online course called:

The Harvest Ledger Circle
How to Launch a Multi-Million Business From Scratch
Sign Up Today!

IMPORTANT: Make the largest and most prominent text on the graphic be: How to Launch a Multi-Million Business From Scratch

For the color scheme of the graphics, let's try a blue color palette; make sure the graphics appeal to both men and women

Make sure each graphic contains 1 of the 3 pics attached (crop pic as needed); and make sure one of the graphics is all TEXT only.

Target Market(s)

men and women looking to start a business

Industry/Entity Type

Entrepreneurship

Colors
0054AA
0677BA
7BADD7
CADEEF
E8F1F8

Requirements
Must have
• All the text and use the 3 pics provided; one graphic can be all text; Simple, modern design that's easy to read

```html
<!DOCTYPE html>
<html lang="en">
<head>
<meta charset="utf-8">
<title>Oakline Push – The Harvest Ledger Circle social graphics</title>
<link rel="stylesheet" href="https://fonts.googleapis.com/css2?family=Oswald:wght@500;700&display=swap">
<style>
  :root{
    --blue-deep:#0054AA;
    --blue-mid:#0677BA;
    --blue-soft:#7BADD7;
    --blue-pale:#CADEEF;
    --blue-mist:#E8F1F8;
    --navy:#0b2a5c;
    --white:#ffffff;
    --stage:#8f8f8f;
    --photo-a:#6b4a3c;
    --photo-b:#23385e;
  }
  *{box-sizing:border-box;margin:0;padding:0}
  html,body{width:882px;height:1200px;overflow:hidden;background:var(--stage)}
  body{position:relative;font-family:"Oswald",sans-serif}
  .post{position:absolute;width:360px;height:360px;overflow:hidden;background:var(--white)}
  .post--blue{background:linear-gradient(160deg,var(--blue-mid),var(--blue-deep))}
  .p1{left:69px;top:36px}.p2{left:453px;top:36px}
  .p3{left:69px;top:420px}.p4{left:453px;top:420px}
  .p5{left:69px;top:804px}.p6{left:453px;top:804px}
  .shape{position:absolute;left:0;top:0;width:360px;height:360px}
  .course-name{position:absolute;font-weight:700;font-size:16px;letter-spacing:.3px;text-transform:uppercase;white-space:nowrap;padding:4px 10px;line-height:1}
  .course-name--band{background:var(--white);color:var(--blue-deep)}
  .course-name--blueband{background:var(--blue-deep);color:var(--white)}
  .course-name--plain{color:var(--blue-deep);padding:0}
  .headline{position:absolute;font-weight:700;text-transform:uppercase;line-height:1.08;letter-spacing:.2px;white-space:nowrap}
  .headline span{display:block}
  .headline--navy{color:var(--navy)}
  .headline--white{color:var(--white)}
  .headline--center{left:0;width:360px;text-align:center}
  .photo{position:absolute;background:linear-gradient(180deg,var(--blue-mist) 0%,var(--photo-a) 45%,var(--photo-b) 100%)}
  .badge{position:absolute;width:80px;height:80px;border-radius:50%;background:var(--white);border:3px solid var(--blue-deep);
    display:flex;flex-direction:column;align-items:center;justify-content:center;color:var(--blue-deep);
    font-weight:700;font-size:16px;line-height:1;text-transform:uppercase;transform:rotate(-10deg)}
  .badge--blue{background:var(--blue-deep);color:var(--white);border-color:var(--white)}
</style>
</head>
<body>

<section class="post p1">
  <svg class="shape" viewBox="0 0 360 360" aria-hidden="true">
    <path d="M0 250 C90 210 200 280 360 220 L360 360 L0 360Z" fill="var(--blue-deep)"/>
    <path d="M0 262 C110 228 210 296 360 238 L360 252 C210 310 110 244 0 276Z" fill="var(--blue-soft)"/>
  </svg>
  <p class="course-name course-name--plain" style="left:0;width:360px;text-align:center;top:16px">The Harvest Ledger Circle</p>
  <h2 class="headline headline--navy headline--center" style="top:42px;font-size:27px">
    <span>How to launch a</span><span>multi-million business</span><span>from scratch</span>
  </h2>
  <div class="photo" style="left:30px;top:142px;width:200px;height:218px" role="img" aria-label="Photo of a smiling entrepreneur couple"></div>
  <div class="badge" style="left:258px;top:240px"><span>Sign up</span><span>today!</span></div>
</section>

<section class="post post--blue p2">
  <svg class="shape" viewBox="0 0 360 360" aria-hidden="true">
    <path d="M0 280 C70 250 120 320 200 360 L0 360Z" fill="var(--white)"/>
  </svg>
  <p class="course-name course-name--band" style="left:0;top:12px">The Harvest Ledger Circle</p>
  <h2 class="headline headline--white" style="left:16px;top:46px;font-size:28px">
    <span>How to launch a</span><span>multi-million</span><span>business</span><span>from scratch</span>
  </h2>
  <div class="photo" style="left:210px;top:160px;width:150px;height:200px" role="img" aria-label="Photo of a businesswoman and businessman"></div>
  <div class="badge" style="left:266px;top:96px"><span>Sign up</span><span>today!</span></div>
</section>

<section class="post p3">
  <div class="photo" style="left:60px;top:40px;width:220px;height:178px" role="img" aria-label="Photo of a confident entrepreneur couple"></div>
  <svg class="shape" viewBox="0 0 360 360" aria-hidden="true">
    <path d="M0 218 C120 204 240 230 360 210 L360 360 L0 360Z" fill="var(--blue-deep)"/>
  </svg>
  <p class="course-name course-name--plain" style="left:0;width:360px;text-align:center;top:14px">The Harvest Ledger Circle</p>
  <div class="badge badge--blue" style="left:262px;top:92px"><span>Sign up</span><span>today!</span></div>
  <h2 class="headline headline--white headline--center" style="top:240px;font-size:27px">
    <span>How to launch a</span><span>multi-million business</span><span>from scratch</span>
  </h2>
</section>

<section class="post post--blue p4">
  <svg class="shape" viewBox="0 0 360 360" aria-hidden="true">
    <path d="M0 40 L360 40 L360 210 C240 230 120 190 0 215Z" fill="var(--blue-mist)"/>
  </svg>
  <p class="course-name course-name--band" style="left:0;width:360px;text-align:center;top:10px">The Harvest Ledger Circle</p>
  <div class="photo" style="left:40px;top:40px;width:220px;height:168px" role="img" aria-label="Photo of two entrepreneurs presenting"></div>
  <div class="badge" style="left:266px;top:60px"><span>Sign up</span><span>today!</span></div>
  <h2 class="headline headline--white headline--center" style="top:240px;font-size:27px">
    <span>How to launch a</span><span>multi-million business</span><span>from scratch</span>
  </h2>
</section>

<section class="post post--blue p5">
  <svg class="shape" viewBox="0 0 360 360" aria-hidden="true">
    <path d="M220 360 C250 300 310 270 360 265 L360 360Z" fill="var(--blue-soft)"/>
  </svg>
  <p class="course-name course-name--band" style="left:16px;top:12px">The Harvest Ledger Circle</p>
  <h2 class="headline headline--white" style="left:16px;top:42px;font-size:27px">
    <span>How to launch a</span><span>multi-million business</span><span>from scratch</span>
  </h2>
  <div class="photo" style="left:16px;top:146px;width:200px;height:214px" role="img" aria-label="Photo of a businessman and businesswoman in suits"></div>
  <div class="badge" style="left:252px;top:244px"><span>Sign up</span><span>today!</span></div>
</section>

<section class="post p6">
  <svg class="shape" viewBox="0 0 360 360" aria-hidden="true">
    <rect x="0" y="46" width="360" height="214" fill="var(--blue-deep)"/>
    <path d="M0 300 C100 270 220 330 360 285 L360 360 L0 360Z" fill="var(--blue-pale)"/>
    <path d="M0 325 C120 300 220 350 360 315 L360 360 L0 360Z" fill="var(--blue-mid)"/>
  </svg>
  <p class="course-name course-name--plain" style="left:0;width:360px;text-align:center;top:15px">The Harvest Ledger Circle</p>
  <h2 class="headline headline--white headline--center" style="top:66px;font-size:40px">
    <span>How to launch</span><span>a multi-million</span><span style="font-size:27px">business from scratch</span>
  </h2>
  <div class="badge" style="left:140px;top:244px"><span>Sign up</span><span>today!</span></div>
</section>

</body>
</html>
```